Quillbrookes websites redesign

Www.quill-brookes.com needs to be redesigned along with updations. The incremental material will be provided for the updations. We are looking for complete redesign of the pages with the new content. The complete write up will be provided soon

Target Market(s)

Global

Coding

Coded - Design and coding required

Number of Pages Required

5+ page

Requirements
Must have
• A clean and slick design for the Consulting.
Should not have
• Too many pictures which reduces the speed of the site

```html
<!DOCTYPE html>
<html lang="en">
<head>
<meta charset="utf-8">
<title>Quillbrookes Consultancy</title>
<link href="https://fonts.googleapis.com/css2?family=Mulish:wght@400;600&family=Arimo:wght@400;700&family=Noto+Serif:ital@1&display=swap" rel="stylesheet">
<style>
:root{
  --blue:#2a9fd0;
  --ink:#444;
  --muted:#777;
  --line:#d8d8d8;
  --hero:#f0f0f0;
  --footer:#1c1c1c;
  --footer-text:#9a9a9a;
  --white:#fff;
}
*{margin:0;padding:0;box-sizing:border-box}
html,body{width:1032px;height:1200px;overflow:hidden;background:var(--white)}
body{position:relative;font-family:"Arimo",Arial,sans-serif;color:var(--ink)}
.abs{position:absolute}
.heading{font-family:"Mulish",Arial,sans-serif}

/* header */
.site-header{left:0;top:0;width:1032px;height:54px;background:var(--white)}
.brand{left:232px;top:12px;display:flex;align-items:center;gap:8px;font-family:"Mulish",sans-serif;font-size:21px;font-weight:600;color:#2d3e50}
.brand-dot{width:24px;height:24px;border-radius:50%;background:var(--blue)}
.main-nav{right:27px;top:0;display:flex;gap:0;height:54px}
.main-nav a{display:block;padding:0 10px;line-height:56px;font-family:"Mulish",sans-serif;font-size:8.5px;font-size:8.6px;color:#555;text-decoration:none;font-size:8.8px}
.main-nav a{font-size:8.8px}
.main-nav a{font-size:9px}
.main-nav a.active{color:var(--blue);box-shadow:inset 0 -3px 0 var(--blue)}

/* hero */
.hero{left:0;top:54px;width:1032px;height:280px;background:var(--hero)}
.hero-map{left:232px;top:58px;width:344px;height:176px;border-radius:40px 60px 30px 50px;background:linear-gradient(120deg,#e6b81a 0%,#1a8bd0 45%,#d44a1c 70%,#e6b81a 100%);opacity:.85}
.hero-title{left:569px;top:105px;font-size:15px;font-weight:600;color:var(--blue)}
.hero-sub{left:569px;top:124px;font-size:15px;color:#444}
.hero-copy{left:569px;top:150px;width:232px;font-size:8px;line-height:12.5px;color:#555}

/* welcome */
.welcome-title{left:0;width:1032px;top:376px;text-align:center;font-size:15px;color:#444;letter-spacing:.3px}
.welcome-sub{left:0;width:1032px;top:403px;text-align:center;font-size:6.8px;color:#333}
.welcome-sub span{color:var(--blue)}
.welcome-rule{left:501px;top:423px;width:31px;height:1px;background:#999}
.welcome-copy{left:336px;top:435px;width:360px;text-align:center;font-size:7px;line-height:11.4px;color:#555}
.btn{left:481px;top:489px;width:70px;height:20px;border:1px solid #bbb;text-align:center;line-height:18px;font-size:7px;color:#555;letter-spacing:.3px}

/* services */
.service{top:546px;width:124px;text-align:center}
.service svg{display:block;margin:0 auto;width:28px;height:28px}
.service h3{margin-top:12px;font-family:"Mulish",sans-serif;font-weight:400;font-size:10px;color:#444;padding-bottom:8px;border-bottom:1px solid var(--line)}
.service.active h3{color:var(--blue)}
.service p{margin-top:8px;font-size:6.8px;line-height:12.4px;color:#777}
.service .more{display:inline-block;margin-top:6px;font-family:"Noto Serif",serif;font-style:italic;font-size:7.5px;color:#888;padding-bottom:4px}
.service.active .more{color:var(--blue);border-bottom:1px solid var(--blue)}

/* consultancy */
.section-rule{top:728px;height:1px;background:var(--line)}
.section-title{left:0;width:1032px;top:721px;text-align:center;font-size:11.5px;color:#666;letter-spacing:.4px}
.photo{top:762px;width:257px;height:89px}
.photo-a{left:232px;background:linear-gradient(90deg,#b07a76 0%,#e8c6bf 45%,#d9aaa2 70%,#6e3b3a 100%)}
.photo-b{left:543px;background:linear-gradient(90deg,#a9c3e0 0%,#cfdcec 45%,#f1d7dc 60%,#9fb7d6 100%)}
.photo-arrow{width:20px;height:17px;display:flex;align-items:center;justify-content:center}
.case-title{top:868px;font-size:10px;color:#555;letter-spacing:.2px}
.case-title.active{color:var(--blue)}
.case-copy{top:886px;width:256px;font-size:7px;line-height:12.4px;color:#888}

/* footer */
.site-footer{left:0;top:970px;width:1032px;height:230px;background:var(--footer)}
.foot-brand{left:232px;top:1010px;display:flex;align-items:center;gap:6px;font-family:"Mulish",sans-serif;font-size:14px;color:#aaa}
.foot-brand i{width:20px;height:20px;border-radius:50%;background:#888;display:block}
.foot-address{left:234px;top:1044px;font-size:7px;line-height:12.4px;color:var(--footer-text)}
.foot-contact{left:234px;top:1105px;font-size:7.2px;line-height:13px;color:var(--footer-text)}
.foot-contact b{color:var(--blue)}
.foot-contact u{color:var(--blue)}
.foot-head{top:1013px;font-family:"Mulish",sans-serif;font-size:8.5px;font-weight:600;color:#ddd;letter-spacing:.2px}
.foot-head::after{content:"";display:block;width:18px;height:1px;background:#888;margin-top:8px}
.foot-note{left:415px;top:1044px;font-size:7px;color:var(--footer-text)}
.mail{left:415px;top:1064px;width:130px;height:24px;border:1px solid #555;font-size:7px;color:#aaa;padding:0 8px;line-height:22px}
.mail svg{position:absolute;right:6px;top:7px}
.site-links{left:598px;top:1043px;list-style:none;font-size:7px;line-height:15.5px;color:#aaa}
.site-links li::before{content:"»";color:#666;margin-right:6px}
.site-links li.active span{color:var(--blue);text-decoration:underline}
.socials{left:718px;top:1044px;display:flex;gap:4px}
.socials i{display:block;width:18px;height:18px;border-radius:50%;border:1px solid #bbb}
.socials i.active{border-color:var(--blue)}
.foot-bottom{left:0;top:1164px;width:1032px;height:1px;background:#333}
.copyright{left:232px;top:1178px;font-size:7px;color:#888}
</style>
</head>
<body>

<header class="site-header abs">
  <div class="brand abs"><span class="brand-dot"></span>Quillbrookes</div>
  <nav class="main-nav abs">
    <a class="active">home</a><a>founder</a><a>consultancy</a><a>system</a><a>case studies</a><a>contact</a>
  </nav>
</header>

<section class="hero abs">
  <div class="hero-map abs" role="img" aria-label="World map coloured by merchandising trade value per region, with value range labels"></div>
</section>
<div class="hero-title abs heading">World Merchandising Trade</div>
<div class="hero-sub abs heading">2012 ( USD Billion)</div>
<p class="hero-copy abs">We invest actively in developing technology platform for better distribution, disintermediation, efficient process flow and cost effective delivery of solutions.</p>

<h1 class="welcome-title abs heading" style="font-weight:400">WELCOME TO QUILLBROOKES</h1>
<p class="welcome-sub abs">WE BUILD LONG LASTING RELATIONSHIPS WITH ALL OUR <span>CLIENTS AND PARTNERS</span></p>
<div class="welcome-rule abs"></div>
<p class="welcome-copy abs">Quillbrookes Consultancy Limited capitalizes on synergies arising from trade and investment linkages between countries and knowledge of traditional and non-traditional pools of liquidity to provide consultancy services to Emerging country banks, Corporates and SMEs.</p>
<div class="btn abs">CONTACT US</div>

<div class="service abs" style="left:232px">
  <svg viewBox="0 0 28 28"><rect x="2" y="18" width="6" height="9" fill="#777"/><rect x="10" y="13" width="6" height="14" fill="#777"/><rect x="18" y="9" width="6" height="18" fill="#777"/><path d="M3 15 L11 8 L16 11 L25 3" stroke="#777" stroke-width="2" fill="none"/><path d="M20 2 H26 V8" stroke="#777" stroke-width="2" fill="none"/></svg>
  <h3>Export Credit Agency</h3>
  <p>Quillbrookes Consultancy Limited (QCL) was exclusively appointed to arrange debt for this project.</p>
  <span class="more">read more</span>
</div>
<div class="service active abs" style="left:379px">
  <svg viewBox="0 0 28 28"><circle cx="14" cy="9" r="5" fill="#2a9fd0"/><circle cx="20" cy="3" r="2.5" fill="#2a9fd0"/><path d="M2 17 C6 15 9 18 14 18 C18 18 20 16 26 15 L24 22 C18 25 9 25 4 22 Z" fill="#2a9fd0"/></svg>
  <h3>Regional/Local banks</h3>
  <p>Quillbrookes Consultancy Limited (QCL) was exclusively appointed to arrange debt for this project.</p>
  <span class="more">read more</span>
</div>
<div class="service abs" style="left:529px">
  <svg viewBox="0 0 28 28"><circle cx="14" cy="14" r="12" fill="#777"/><text x="14" y="19" text-anchor="middle" font-family="Arimo,sans-serif" font-size="15" font-weight="700" fill="#fff">$</text></svg>
  <h3>Structured Financing</h3>
  <p>Quillbrookes Consultancy Limited (QCL) was exclusively appointed to arrange debt for this project.</p>
  <span class="more">read more</span>
</div>
<div class="service abs" style="left:677px">
  <svg viewBox="0 0 28 28"><path d="M13 3 A12 12 0 1 0 25 15 H13 Z" fill="#777"/><path d="M16 1 V12 H27 A11 11 0 0 0 16 1 Z" fill="#777"/></svg>
  <h3>Bank Lines Business</h3>
  <p>Quillbrookes Consultancy Limited (QCL) was exclusively appointed to arrange debt for this project.</p>
  <span class="more">read more</span>
</div>

<div class="section-rule abs" style="left:232px;width:228px"></div>
<div class="section-rule abs" style="left:572px;width:228px"></div>
<h2 class="section-title abs heading" style="font-weight:400">CONSULTANCY</h2>

<div class="photo photo-a abs" role="img" aria-label="Profile photo of a woman with pearl earrings"></div>
<div class="photo-arrow abs" style="left:468px;top:834px;background:var(--blue)"><svg width="10" height="6" viewBox="0 0 10 6"><path d="M0 3H9M6 0L9 3L6 6" stroke="#fff" fill="none"/></svg></div>
<div class="photo photo-b abs" role="img" aria-label="Photo of a person in a blue shirt putting money into a piggy bank"></div>
<div class="photo-arrow abs" style="left:780px;top:834px;background:#333"><svg width="10" height="6" viewBox="0 0 10 6"><path d="M0 3H9M6 0L9 3L6 6" stroke="#fff" fill="none"/></svg></div>

<h3 class="case-title active abs heading" style="left:232px;font-weight:400">PLAIN VANILLA FINANCING SOLUTIONS</h3>
<p class="case-copy abs" style="left:232px">The Consultancy provides access to local/regional banks across Hong Kong, Singapore, Dubai , New York and London and helps corporate clients in diversi-fying their financial partners and adding new banks to their bank group...</p>
<h3 class="case-title abs heading" style="left:542px;font-weight:400">STRUCTURED FINANCING SOLUTIONS</h3>
<p class="case-copy abs" style="left:542px">The Consultancy provides end-to-end structured solutions on the Payables, Receivables or Inventory side for working capital requirements with off/part/on recourse balance sheet structures..</p>

<footer class="site-footer abs"></footer>
<div class="foot-brand abs"><i></i>Quillbrookes</div>
<p class="foot-address abs">Quillbrookes Consultancy Ltd<br>Unit 04, 9th Floor, Harbourline Tower,<br>8 Ferry Quay Road, Kowloon<br>Hong Kong</p>
<p class="foot-contact abs">T: <b>852-27160395</b><br>E: <u>hello@quill-brookes.com</u></p>

<h4 class="foot-head abs" style="left:415px">GET IN TOUCH!</h4>
<p class="foot-note abs">Simply Drop Your Mail Here</p>
<div class="mail abs">Your Email Here<svg width="11" height="8" viewBox="0 0 11 8"><rect x=".5" y=".5" width="10" height="7" fill="none" stroke="#2a9fd0"/><path d="M.5 .5L5.5 4.5L10.5 .5" stroke="#2a9fd0" fill="none"/></svg></div>

<h4 class="foot-head abs" style="left:598px">SITE LINKS</h4>
<ul class="site-links abs">
  <li class="active"><span>Home</span></li><li>Founder</li><li>Consultancy</li><li>System</li><li>Case Studies</li><li>Contact</li>
</ul>

<h4 class="foot-head abs" style="left:718px">SOCIAL LINKS</h4>
<div class="socials abs"><i class="active"></i><i></i><i></i><i></i></div>

<div class="foot-bottom abs"></div>
<p class="copyright abs">© Quillbrookes Consultancy Limited</p>

</body>
</html>
```